Honey packaging lable for small honey producer

We are small scale bee keepers and need a design for labels for our honey.
We curently sell honey in 2 different package sizes, 500gm and 1kg so the label would need to be suitable for both.
The plan is to print the label on brown or "craft" paper with a laser printer to give a rustic feel so the design will need to be monotone.
As we are in Australia all measurements will need to be metric
Label dimensions should be 105mm wide by 59.4mm high (so we can fit 10 labels per sheet of a4 paper).
The batch number, nett weight and number of servings per package on the nutritional label need to be able to be changed to suit the packaging size.
Designs need to be able to be opened and printed from open source software such as Free Sheetwork, Gimp or similar. If proprietary software is used there must be at least a free program to allow printing and basic manipulation of the design.
Updates

Thank you everyone for the designs you submitted. I have been surprised by the quality of work supplied and wish I had the budget to make a payment to everyone, but unfortunately that is not the case :( 

This is my first time doing anything like this and it has been an interesting experience. I have definitely learned lots and hopefully I will be a better and more concise brief writer next time :)

The only other feedback I would like to give is to read the brief carefully. There were some designers that submited color designs which weren't suitable for my needs which may have been avoided.

Thank you again for all your hard work.

All the best.

Dennis & Margaret.

Industry/Entity Type

Printer

Requirements
Must have
• Thornwick Grove
honey
Nett Weight
Batch Number:
Produced by: Dennis and Margaret Halloway, Brackleys Gully, Victoria. 0492 317064

Nutritional panel similar to : http://www.example-jarco.net.au/images/products/jars-pails-L030.jpg
Nice to have
• Produced in the Marlbrooks
Pure, Natural, raw.
Contains traces of pollen and wax
Honey is a natural product and may crystallize. It may be eaten as is or re-liquefied by placing the container in hot water.
Should not have
• No twee cartoon bees or skep bee hives please!

```html
<!DOCTYPE html>
<html lang="en">
<head>
<meta charset="utf-8">
<title>Thornwick Grove Honey – Jar Label</title>
<link rel="stylesheet" href="https://fonts.googleapis.com/css2?family=Courier+Prime:wght@700&family=Michroma&family=Orbitron:wght@900&family=Roboto+Condensed:wght@400;700&display=swap">
<style>
  :root {
    --backdrop: #f1c40f;
    --kraft: #a88a5e;
    --kraft-deep: #8f7348;
    --ink: #121110;
    --panel: #0c0b0a;
    --panel-text: #c9a874;
    --panel-text-soft: #b99867;
  }
  * { margin: 0; padding: 0; box-sizing: border-box; }
  html, body { width: 1200px; height: 900px; overflow: hidden; }
  body {
    background: var(--backdrop);
    font-family: "Roboto Condensed", "Arial Narrow", sans-serif;
  }
  .label {
    position: absolute;
    left: 181px; top: 213px;
    width: 837px; height: 474px;
    box-shadow: 6px 8px 14px rgba(0,0,0,0.35);
  }
  .label-front {
    position: absolute; left: 0; top: 0;
    width: 557px; height: 474px;
    background: radial-gradient(ellipse at 55% 45%, var(--kraft) 0%, var(--kraft) 55%, var(--kraft-deep) 100%);
    color: var(--ink);
  }
  .comb-texture {
    position: absolute; left: 0; top: 24px; width: 557px; height: 300px;
    background: linear-gradient(180deg, rgba(90,70,40,0.16), rgba(90,70,40,0));
  }
  .rule { position: absolute; left: 0; width: 557px; background: var(--ink); }
  .rule.top-thick { top: 12px; height: 6px; }
  .rule.top-thin { top: 22px; height: 2px; }
  .rule.title-above { top: 110px; left: 20px; width: 517px; height: 2px; }
  .rule.title-below-a { top: 160px; left: 20px; width: 517px; height: 4px; }
  .rule.title-below-b { top: 168px; left: 20px; width: 517px; height: 2px; }
  .rule.bottom-thin { top: 432px; height: 2px; }
  .rule.bottom-thick { top: 438px; height: 8px; }

  .farm-name {
    position: absolute; left: 0; top: 116px; width: 557px;
    text-align: center;
    font-family: "Michroma", sans-serif; font-weight: 400;
    font-size: 33px; letter-spacing: 0.5px;
    -webkit-text-stroke: 0.8px var(--ink);
  }
  .product-name {
    position: absolute; left: 0; top: 166px; width: 557px;
    text-align: center;
    font-family: "Orbitron", sans-serif; font-weight: 900;
    font-size: 80px; letter-spacing: 6px; line-height: 1.05;
  }
  .bee {
    position: absolute;
    background: radial-gradient(ellipse, rgba(18,17,16,0.55), rgba(18,17,16,0) 70%);
  }
  .bee.left { left: 26px; top: 186px; width: 82px; height: 52px; }
  .bee.right { left: 448px; top: 186px; width: 82px; height: 52px; }
  .bee.lower { left: 380px; top: 305px; width: 66px; height: 52px; }

  .tagline {
    position: absolute; left: 0; top: 258px; width: 557px; text-align: center;
    font-family: "Courier Prime", monospace; font-weight: 700;
    font-size: 19px; letter-spacing: 0.5px;
  }
  .origin {
    position: absolute; left: 0; top: 288px; width: 557px; text-align: center;
    font-family: "Courier Prime", monospace; font-weight: 700;
    font-size: 13px;
  }
  .net-weight {
    position: absolute; left: 18px; top: 364px;
    font-weight: 700; font-size: 21px; letter-spacing: -0.3px;
  }
  .net-weight .value { margin-left: 14px; }
  .batch {
    position: absolute; left: 18px; top: 393px;
    font-size: 15px; letter-spacing: -0.2px;
  }
  .batch .key { font-weight: 700; }
  .producer {
    position: absolute; right: 18px; top: 356px;
    text-align: right; font-weight: 700; font-size: 13px; line-height: 15px;
  }

  .label-panel {
    position: absolute; left: 557px; top: 0;
    width: 280px; height: 474px;
    background: var(--panel);
    color: var(--panel-text);
  }
  .pack-size {
    position: absolute; left: 190px; top: 10px; width: 84px;
    text-align: center; font-weight: 700; font-size: 19px;
  }
  .nutrition-title {
    position: absolute; left: 24px; top: 56px;
    font-weight: 700; font-size: 17px;
  }
  .serving {
    position: absolute; left: 24px; top: 76px;
    font-size: 15px; line-height: 18px;
  }
  .nutrition-table {
    position: absolute; left: 24px; top: 124px; width: 232px;
    border-collapse: collapse; font-size: 13.5px;
  }
  .nutrition-table th {
    font-weight: 400; text-align: right; font-size: 13px; line-height: 15px;
    padding-bottom: 6px; color: var(--panel-text-soft);
  }
  .nutrition-table td { line-height: 18px; font-weight: 700; }
  .nutrition-table td.num { text-align: right; }
  .nutrition-table .sub { padding-left: 8px; }
  .panel-notes {
    position: absolute; left: 12px; top: 298px; width: 256px;
    text-align: center; font-size: 13px; line-height: 16.5px;
  }
  .panel-notes strong { font-weight: 700; }
  .panel-notes .care { margin-top: 12px; }
  .panel-bee {
    position: absolute; left: 204px; top: 412px; width: 64px; height: 48px;
    background: radial-gradient(ellipse, rgba(201,168,116,0.5), rgba(201,168,116,0) 70%);
  }
</style>
</head>
<body>
  <main class="label">
    <section class="label-front">
      <div class="comb-texture" role="img" aria-label="Faint honeycomb pattern across the kraft paper"></div>
      <div class="rule top-thick"></div>
      <div class="rule top-thin"></div>
      <div class="rule title-above"></div>
      <h1 class="farm-name">THORNWICK GROVE</h1>
      <div class="rule title-below-a"></div>
      <div class="rule title-below-b"></div>
      <div class="bee left" role="img" aria-label="Engraved honey bee illustration"></div>
      <p class="product-name">HONEY</p>
      <div class="bee right" role="img" aria-label="Engraved honey bee illustration"></div>
      <p class="tagline">Natural. Pure. Raw. Not Heat Treated.</p>
      <p class="origin">Produced in the Marlbrooks.</p>
      <div class="bee lower" role="img" aria-label="Engraved honey bee illustration"></div>
      <p class="net-weight">Net Weight:<span class="value">500g</span></p>
      <p class="batch"><span class="key">Batch Number:</span> 130416</p>
      <p class="producer">Produced by:<br>Dennis &amp; Margaret Halloway<br>Brackleys Gully<br>VICTORIA 0492 317064</p>
      <div class="rule bottom-thin"></div>
      <div class="rule bottom-thick"></div>
    </section>

    <aside class="label-panel">
      <p class="pack-size">500g</p>
      <h2 class="nutrition-title">Nutritional Information</h2>
      <p class="serving">Servings per package: 33<br>Serving Size: 15g</p>
      <table class="nutrition-table">
        <thead>
          <tr><th></th><th>Quantity<br>Per Serving</th><th>Quantity<br>Per 100g</th></tr>
        </thead>
        <tbody>
          <tr><td>Energy</td><td class="num">214KJ</td><td class="num">1416KJ</td></tr>
          <tr><td>Protein</td><td class="num">.05g</td><td class="num">.05g</td></tr>
          <tr><td>Fat - Total</td><td class="num">0g</td><td class="num">0g</td></tr>
          <tr><td class="sub">-Saturated</td><td class="num">0g</td><td class="num">0g</td></tr>
          <tr><td>Carbohydrates</td><td class="num">12.5g</td><td class="num">83.1g</td></tr>
          <tr><td class="sub">-sugars*</td><td class="num">12.5g</td><td class="num">82.5g</td></tr>
          <tr><td>Sodium</td><td class="num">2.3mg</td><td class="num">15mg</td></tr>
        </tbody>
      </table>
      <div class="panel-notes">
        <p>*Sugars naturally occuring in honey.<br><strong>Ingredients: Pure 100% Australian Honey</strong><br>Contains traces of pollen and wax.</p>
        <p class="care">Honey is a natural product and may crystalize.<br>It may be eaten as is or re-liquefied by<br>placing the container in hot water.</p>
      </div>
      <div class="panel-bee" role="img" aria-label="Small line-drawn honey bee"></div>
    </aside>
  </main>
</body>
</html>
```